Veldmark Supplies Business Card

Professional business card that stand out to our potential customers. Front and back with clean modern design

Industry/Entity Type

Oil and gas

Contact Information for Business Card

Name, address, website , office phone and cell number

Requirements
Must have
• Editable files for each employee

```html
<!DOCTYPE html>
<html lang="en">
<head>
<meta charset="utf-8">
<title>Veldmark Supplies – Business Card</title>
<link rel="stylesheet" href="https://fonts.googleapis.com/css2?family=Montserrat:wght@400;500;700;800&display=swap">
<style>
  :root {
    --bg: #222222;
    --red: #ff0000;
    --blue: #05b1d4;
    --white: #ffffff;
    --card-w: 330px;
    --card-h: 560px;
    --radius: 26px;
  }
  * { box-sizing: border-box; margin: 0; padding: 0; }
  html, body {
    width: 1200px; height: 711px; overflow: hidden;
    background: var(--bg);
    font-family: "Montserrat", Arial, sans-serif;
  }
  .stage { position: relative; width: 1200px; height: 711px; }
  .card {
    position: absolute; top: 76px;
    width: var(--card-w); height: var(--card-h);
    border-radius: var(--radius); overflow: hidden;
    box-shadow: 0 14px 30px rgba(0,0,0,.55);
  }

  /* Front */
  .card-front { left: 232px; background: var(--red); }
  .front-mark {
    position: absolute; left: 40px; top: 230px;
    display: flex; align-items: center; gap: 14px;
    color: var(--white);
  }
  .front-mark .square { width: 30px; height: 30px; background: var(--white); flex: none; }
  .front-mark .name { font-weight: 800; font-size: 26px; line-height: 1.05; letter-spacing: 1px; text-transform: uppercase; }
  .front-strip {
    position: absolute; right: 24px; top: 40px;
    writing-mode: vertical-rl;
    color: var(--white); font-weight: 800; font-size: 18px; letter-spacing: 3px;
    text-transform: uppercase;
  }

  /* Back */
  .card-back { left: 638px; background: var(--blue); }
  .back-split { position: absolute; inset: 0; }
  .back-header {
    position: absolute; left: 22px; top: 22px;
    color: var(--red); font-weight: 800; font-size: 17px; letter-spacing: 2px;
    text-transform: uppercase;
  }
  .back-mark {
    position: absolute; left: 0; right: 0; top: 112px;
    display: flex; justify-content: center; align-items: center; gap: 12px;
    color: var(--red);
  }
  .back-mark .square { width: 26px; height: 26px; background: var(--red); }
  .back-mark .name { font-weight: 800; font-size: 24px; line-height: 1.05; text-transform: uppercase; letter-spacing: 1px; }
  .person { position: absolute; left: 0; right: 0; top: 280px; text-align: center; color: var(--white); }
  .person-name { font-weight: 800; font-size: 24px; letter-spacing: .5px; text-transform: uppercase; }
  .person-title {
    display: flex; align-items: center; justify-content: center; gap: 10px;
    font-size: 13px; font-weight: 500; margin-top: 2px;
  }
  .person-title::before, .person-title::after { content: ""; width: 70px; height: 1.5px; background: var(--white); }
  .icon-row { position: absolute; left: 0; right: 0; top: 352px; display: flex; justify-content: center; gap: 12px; }
  .icon { width: 30px; height: 26px; background: var(--red); display: flex; align-items: center; justify-content: center; }
  .icon svg { width: 16px; height: 16px; }
  .contact-list {
    position: absolute; left: 0; right: 0; top: 392px;
    list-style: none; text-align: center; color: var(--white);
    font-size: 13px; line-height: 1.5; font-weight: 500;
  }
  .divider { position: absolute; left: 50px; right: 50px; top: 480px; height: 1.5px; background: var(--white); }
  .address { position: absolute; left: 0; right: 0; top: 490px; text-align: center; color: var(--white); font-size: 13px; line-height: 1.5; font-weight: 500; }
</style>
</head>
<body>
<main class="stage">

  <section class="card card-front" aria-label="Card front">
    <div class="front-mark">
      <span class="square"></span>
      <span class="name">Veldmark<br>Supplies</span>
    </div>
    <div class="front-strip">Veldmark Supplies</div>
  </section>

  <section class="card card-back" aria-label="Card back">
    <svg class="back-split" viewBox="0 0 330 560" preserveAspectRatio="none" aria-hidden="true">
      <polygon points="0,0 330,0 330,150 0,265" fill="#ffffff"/>
    </svg>
    <div class="back-header">Veldmark Supplies</div>
    <div class="back-mark">
      <span class="square"></span>
      <span class="name">Veldmark<br>Supplies</span>
    </div>

    <div class="person">
      <div class="person-name">Dalen Ortwick</div>
      <div class="person-title">President</div>
    </div>

    <div class="icon-row">
      <span class="icon" aria-label="Phone">
        <svg viewBox="0 0 16 16"><path d="M2 5c0-2 2-3 6-3s6 1 6 3v1h-3V5H5v1H2z M4 8h8l1 6H3z" fill="#fff"/></svg>
      </span>
      <span class="icon" aria-label="Mobile">
        <svg viewBox="0 0 16 16"><rect x="4.5" y="1" width="7" height="14" rx="1.5" fill="none" stroke="#fff" stroke-width="1.5"/><circle cx="8" cy="12.5" r="0.9" fill="#fff"/></svg>
      </span>
      <span class="icon" aria-label="Email">
        <svg viewBox="0 0 16 16"><rect x="1.5" y="3.5" width="13" height="9" fill="none" stroke="#fff" stroke-width="1.5"/><path d="M1.5 3.5 8 9l6.5-5.5" fill="none" stroke="#fff" stroke-width="1.5"/></svg>
      </span>
      <span class="icon" aria-label="Website">
        <svg viewBox="0 0 16 16"><circle cx="8" cy="8" r="6.5" fill="none" stroke="#fff" stroke-width="1.5"/><path d="M1.5 8h13M8 1.5c-3 3.5-3 9.5 0 13M8 1.5c3 3.5 3 9.5 0 13" fill="none" stroke="#fff" stroke-width="1.2"/></svg>
      </span>
    </div>

    <ul class="contact-list">
      <li>555-214-3307</li>
      <li>000-000-9999</li>
      <li>info@example-youremail.com</li>
      <li>www.example-yourwebsite.com</li>
    </ul>
    <div class="divider"></div>
    <p class="address">482 Harlow Ave, Ste<br>100, Brenton, TX 75204</p>
  </section>

</main>
</body>
</html>
```